Copperleaf Balustrade Website Redesign

I want a fresh new design for my website. Original website
www.copperleafbalustrade-example.com. Will need to add additional photos for winning designer. Please use the basic layout for new design. Looking to get a more modern, functional site to attract new customer and ne bale to highlight past projects. Need it to be easy to navigate and get in touch with me for inquiries.

Target Market(s)

Builders and home owners in WA state

Industry/Entity Type

Building, Construction, Deck building

Coding

Coded - Design and coding required

Number of Pages Required

5+ page

Font styles to use
Sans Serif

Colors
0054AA
0677BA
7BADD7
CADEEF
E8F1F8
0094D4
00A9DD
6FCCEA
C7EBF8
E9F6FB
00AB8E
00BBA5
67D7C9
C6EFE9
E9F9F6
59FF00
82FF00
B8FF75
E3FFCB
F4FFEA

Requirements
Must have
• Will need to add more photos of completed projects
Nice to have
• Fresh take on old website, something modern
Should not have
• Nothing comes to mind

```html
<!DOCTYPE html>
<html lang="en">
<head>
<meta charset="utf-8">
<title>Why Choose Us – Copperleaf Balustrade</title>
<link rel="stylesheet" href="https://fonts.googleapis.com/css2?family=Inter:wght@500;600;700;800&family=Jost:wght@400;500&display=swap">
<style>
:root{
  --brand:#0054AA;
  --brand-mid:#0677BA;
  --accent:#00A9DD;
  --accent-light:#6FCCEA;
  --teal:#00AB8E;
  --ink:#111111;
  --body:#3a3a3a;
  --white:#ffffff;
  --footer-bg:#000000;
}
*{margin:0;padding:0;box-sizing:border-box}
html,body{width:1200px;height:2412px;overflow:hidden;background:var(--white)}
body{font-family:"Jost",sans-serif;color:var(--body);position:relative}
.site-header{position:absolute;top:0;left:0;width:1200px;height:92px}
.brand{position:absolute;left:58px;top:22px;display:flex;align-items:center;gap:10px}
.brand-square{width:30px;height:30px;background:var(--brand)}
.brand-name{font-family:"Inter",sans-serif;font-weight:700;font-size:20px;line-height:22px;color:var(--brand);letter-spacing:.5px;text-transform:uppercase}
.main-nav{position:absolute;top:31px;right:55px;display:flex;align-items:center;font-family:"Inter",sans-serif;font-weight:600;font-size:14px;color:var(--ink)}
.main-nav a{color:inherit;text-decoration:none;margin-left:48px}
.main-nav a.is-active{color:var(--brand-mid)}
.main-nav a.nav-cta{background:var(--brand);color:var(--white);padding:10px 11px;margin-left:47px}
.hero{position:absolute;top:92px;left:0;width:1200px;height:343px;background:linear-gradient(100deg,#8b8378 0%,#a9a196 30%,#c9c8c5 60%,#d8d8d8 100%)}
.hero-title{position:absolute;left:57px;top:142px;font-family:"Inter",sans-serif;font-weight:800;font-size:40px;color:var(--white)}
.intro{position:absolute;top:470px;left:0;width:1200px;text-align:center}
.intro h2{font-family:"Inter",sans-serif;font-weight:800;font-size:25px;color:var(--brand)}
.intro p{margin-top:14px;font-size:13.5px;line-height:20px;color:var(--ink)}
.feature{position:absolute;left:56px;width:1089px;height:347px}
.feature-photo{position:absolute;top:0;width:505px;height:347px}
.feature-text{position:absolute;width:545px}
.feature h3{font-family:"Inter",sans-serif;font-weight:800;font-size:25px;color:var(--brand);text-transform:uppercase;white-space:nowrap}
.feature p{margin-top:14px;font-size:13.5px;line-height:20px}
.feature.photo-left .feature-photo{left:0}
.feature.photo-left .feature-text{left:546px}
.feature.photo-right .feature-photo{right:0}
.feature.photo-right .feature-text{left:0}
.site-footer{position:absolute;top:2147px;left:0;width:1200px;height:265px;background:var(--footer-bg);color:var(--white)}
.footer-brand{position:absolute;left:58px;top:44px;display:flex;align-items:center;gap:10px}
.footer-brand .brand-square{width:44px;height:44px;background:var(--accent)}
.footer-brand .brand-name{font-size:24px;line-height:28px;color:var(--accent);font-weight:500}
.footer-about{position:absolute;left:58px;top:133px;width:325px;font-size:13.5px;line-height:20px}
.footer-col{position:absolute;top:45px}
.footer-col h4{font-family:"Inter",sans-serif;font-weight:600;font-size:13.5px;color:var(--accent-light);text-transform:uppercase}
.footer-col ul{list-style:none;margin-top:14px}
.footer-col li{font-size:13.5px;height:30.7px;display:flex;align-items:center}
.footer-col li::before{content:"";width:6px;height:6px;background:var(--accent);transform:rotate(45deg);margin:0 14px 0 3px}
.col-links{left:505px}
.col-products{left:726px}
.col-social{left:986px;top:43px}
.social-row{display:flex;gap:10px;margin-top:18px}
.social-row span{width:30px;height:30px;border-radius:50%;background:var(--teal)}
.footer-rule{position:absolute;left:0;top:217px;width:1200px;height:1px;background:#444}
.copyright{position:absolute;top:229px;width:1200px;text-align:center;font-size:13.5px}
</style>
</head>
<body>
<header class="site-header">
  <div class="brand"><span class="brand-square"></span><span class="brand-name">Copperleaf<br>Balustrade</span></div>
  <nav class="main-nav">
    <a href="#">HOME</a><a href="#">ABOUT</a><a href="#">PRODUCTS</a><a href="#" class="is-active">WHY CHOOSE US</a><a href="#" class="nav-cta">CONTACT</a>
  </nav>
</header>

<section class="hero" role="img" aria-label="Hands sketching architectural floor plans with pencils beside a laptop and calculator">
  <h1 class="hero-title">WHY CHOOSE US</h1>
</section>

<section class="intro">
  <h2>WHY CHOOSE COPPERLEAF BALUSTRADE?</h2>
  <p>Lorem ipsum dolor sit amet, consectetur adipiscing elit, sed do eiusmod tempor incididunt ut labore et dolore magna aliqua.<br>Quis ipsum suspendisse ultrices gravida. Risus commodo viverra maecenas accumsan lacus vel facilisis.</p>
</section>

<article class="feature photo-left" style="top:592px">
  <div class="feature-photo" role="img" aria-label="Installer fitting a cable railing post on wooden deck stairs" style="background:linear-gradient(135deg,#9aa0a3 0%,#b07a55 45%,#8e5a3a 100%)"></div>
  <div class="feature-text" style="top:123px;width:545px">
    <h3>Locally Crafted, Regionally Resilient</h3>
    <p>Our railings are designed with the Pacific Northwest's weather in mind—rain, snow, and everything in between. We use durable materials that are resistant to corrosion, moisture, and the elements, ensuring your railings stand the test of time.</p>
  </div>
</article>

<article class="feature photo-right" style="top:976px">
  <div class="feature-photo" role="img" aria-label="Three-storey white house with glass balcony railings" style="background:linear-gradient(160deg,#d9d9d6 0%,#cfcfc9 40%,#5b5f52 80%,#6a6450 100%)"></div>
  <div class="feature-text" style="top:123px;width:545px">
    <h3>Custom Solutions for Every Need</h3>
    <p>We work closely with you to design and fabricate custom railing systems that perfectly suit<br>your space, style, and functional requirements. From intricate designs to minimalistic finishes,<br>we tailor every project to your vision.</p>
  </div>
</article>

<article class="feature photo-left" style="top:1360px">
  <div class="feature-photo" role="img" aria-label="Deck with black-framed glass railing overlooking a valley town" style="background:linear-gradient(180deg,#b9cde0 0%,#8a9a86 35%,#6d7560 60%,#8f9496 100%)"></div>
  <div class="feature-text" style="top:123px;width:545px">
    <h3>Expert Installation &amp; Craftsmanship</h3>
    <p>Our skilled craftsmen take pride in delivering exceptional workmanship, while our<br>professional installers ensure every railing is securely mounted and aligned to meet local<br>safety codes.</p>
  </div>
</article>

<article class="feature photo-right" style="top:1745px">
  <div class="feature-photo" role="img" aria-label="Grey home with glass balcony railing above a patio with outdoor furniture" style="background:linear-gradient(170deg,#e6e8ea 0%,#7d8083 40%,#5d6064 65%,#a9a7a3 100%)"></div>
  <div class="feature-text" style="top:123px;left:3px;width:545px">
    <h3>Full-Service Partner</h3>
    <p>From the initial consultation and design process to installation and ongoing maintenance, we<br>are with you every step of the way to ensure your project exceeds expectations.</p>
  </div>
</article>

<footer class="site-footer">
  <div class="footer-brand"><span class="brand-square"></span><span class="brand-name">COPPERLEAF<br>BALUSTRADE</span></div>
  <p class="footer-about">we specialize in crafting custom railing systems designed to withstand the region's unique climate while enhancing the beauty of your outdoor living spaces.</p>
  <div class="footer-col col-links">
    <h4>Quick Links</h4>
    <ul><li>Home</li><li>Product</li><li>Why Choose us</li><li>Contact</li></ul>
  </div>
  <div class="footer-col col-products">
    <h4>Our Product</h4>
    <ul><li>Aluminum Railings</li><li>Glass Railings</li><li>Cable Railings</li><li>Custom design</li></ul>
  </div>
  <div class="footer-col col-social">
    <h4>Connect With Us</h4>
    <div class="social-row"><span></span><span></span><span></span><span></span></div>
  </div>
  <div class="footer-rule"></div>
  <p class="copyright">© Copyright 2024&nbsp; All Rights Reserved</p>
</footer>
</body>
</html>
```